IV Nutritional Clinic Web Design

We are working with Velqo. They are an IV Nutritional Clinic and in need of a new website design.
Some sites to use for inspiration:
https://brightpathcareco.com
https://www.ourzavrowellness.com
https://www.dewspringlounge.com
https://qvitalsurge.com
https://www.lumo-vital.com/pages/iv-therapy-west-hollywood
https://www.tqoncologyhub.com/cancer-care/iv-drips/
https://dripwellary.com
https://corvinahealthhub.com
Thank you for taking the time to consider designing a website for us. We are web developers based in Stockton, CA, USA. Most of our projects go through the same process. Understanding this process may help you win a project with us. We custom-code all of our websites in-house. We don’t have any requirements as to what tools you use for your design, but we prefer Figma files. For any design that we label as four-stars, we send it to the client for review. The client picks the final design they want us to use. Once we complete this process, we will continue to show additional clients all the four-star sites and purchase them later. Your designs will have multiple chances to sell. For better chances of success, we ask that you follow these guidelines.
IMAGES:
If you use any images or icons in the design, we ask that you have a link to the asset so we can purchase the image/icon. Most of the designs we submit do not have the customer’s images on them unless they have some great images. Be creative; show us the feeling you are trying to portray with your image choices. Use any royalty-free site you choose. We subscribe to Pixvane and mainly use their images, but we can purchase images outside of Pixvane.
PLEASE NOTE: we will not submit designs to clients with watermarks on the images.
FONTS:
We ask that you identify the fonts used in the design. This can be done in a message if you want. We typically use Google Fonts and Pixvane Fonts.
CONTENT:
We're always open to different content and ideas. We often submit designs with stock images so the client can see our vision. We typically take pictures after the website launch to use their images with our vision. Lorem Ipsum is fine for paragraphs, but we ask that you write the headers in correct English. We want to be able to show the vision and identify the sections of the website.
INSPIRATION:
We typically add a couple of links in the brief of websites we like to help you get started in your design.
REVISIONS:
We do not often ask for revisions of the designs unless we see something in the design that may not appeal to the client. If there are slight changes that we want to make, we do that in the development process.
FEEDBACK:
We rarely give feedback on designs during the design process. We are working on many website projects and do not have the time to provide feedback. We usually respond if your request is well thought out and asks specific questions, but a note asking “feedback, please” usually goes unanswered.

```html
<!DOCTYPE html>
<html lang="en">
<head>
<meta charset="utf-8">
<title>Velqo Hydration — IV Nutritional Clinic</title>
<link href="https://fonts.googleapis.com/css2?family=Quicksand:wght@600;700&family=Montserrat:wght@400;500;600;700&display=swap" rel="stylesheet">
<style>
:root{
  --navy:#1c2786;
  --navy-deep:#141c63;
  --blue:#2a45d0;
  --green:#6b9b2e;
  --green-dark:#557d22;
  --ink:#222;
  --muted:#555;
  --light:#f1f1f1;
  --line:#c9c9c9;
  --footer:#232323;
  --white:#fff;
}
*{box-sizing:border-box;margin:0;padding:0}
html,body{width:1200px;height:4201px;overflow:hidden}
body{font-family:'Montserrat',sans-serif;color:var(--ink);background:var(--white);position:relative}
.head{font-family:'Quicksand',sans-serif;font-weight:700;color:var(--navy)}
.eyebrow{font-family:'Montserrat',sans-serif;font-weight:600;color:var(--green);font-size:20px}
.btn{display:inline-block;background:var(--green);color:var(--white);font-weight:600;font-size:13px;border-radius:30px;padding:0 20px;line-height:37px}
section,header,footer,.topbar{position:absolute;left:0;width:1200px}
.abs{position:absolute}

/* top bar */
.topbar{top:0;height:36px;background:var(--navy-deep);color:var(--white);font-size:12px}
.topbar .item{position:absolute;top:10px;display:flex;align-items:center;gap:8px}
.topbar .social{position:absolute;right:16px;top:10px;display:flex;gap:10px}
.dot{width:16px;height:16px;border-radius:50%;background:var(--white);display:inline-block}
.topbar .social .dot{width:14px;height:14px}

/* header */
header{top:36px;height:95px;background:var(--white)}
.logo{position:absolute;left:66px;top:22px;font-family:'Montserrat',sans-serif;font-weight:700;font-size:36px;color:var(--navy);letter-spacing:1px}
.nav{position:absolute;left:354px;top:38px;display:flex;gap:40px;font-size:15px;font-weight:600}
.nav .active{text-decoration:underline;text-underline-offset:5px}
header .btn{position:absolute;right:58px;top:28px;line-height:38px;font-size:13px}

/* hero */
.hero{top:131px;height:542px}
.hero-photo{position:absolute;inset:0;background:linear-gradient(90deg,#3d3836 0%,#5d5855 38%,#a8a7a8 62%,#dadcdf 100%)}
.hero-text{position:absolute;left:63px;top:140px;width:410px;color:var(--white)}
.hero-text .welcome{font-weight:600;font-size:20px}
.hero-text h1{font-family:'Quicksand',sans-serif;font-weight:600;font-size:50px;line-height:63px;margin-top:14px}
.hero-text p{font-size:14.5px;line-height:22px;margin-top:14px}
.hero-text .btn{margin-top:24px;line-height:37px}
.slider{position:absolute;display:flex;gap:5px}
.slider span{height:6px;border-radius:3px;width:18px;background:var(--white)}
.slider span:first-child{width:36px}

/* about */
.about{top:673px;height:639px;background:var(--light)}
.about-photo{position:absolute;left:68px;top:96px;width:468px;height:467px;border:3px solid var(--navy);border-radius:30px;background:linear-gradient(160deg,#d9dde2,#8fa3b4 55%,#516a7d)}
.about-body{position:absolute;left:593px;top:112px;width:540px}
.about-body h2{font-size:50px;line-height:63px;margin-top:18px}
.about-body p{font-size:14px;line-height:22px;margin-top:24px;color:var(--ink)}
.features{display:grid;grid-template-columns:180px 200px;row-gap:17px;margin-top:22px;font-size:12.5px;font-weight:600}
.features li{list-style:none;display:flex;align-items:center;gap:10px}
.about-body .btn{margin-top:30px;line-height:37px}

/* services */
.services{top:1312px;height:644px;text-align:center}
.services .eyebrow{position:absolute;top:80px;width:100%}
.services h2{position:absolute;top:124px;width:100%;font-size:50px;line-height:62px}
.card{position:absolute;top:277px;height:300px;background:#f3f3f3;border:1px solid #ddd;box-shadow:0 3px 6px rgba(0,0,0,.15);padding:20px 10px 0}
.card .icon{width:122px;height:122px;border-radius:50%;background:#6e6e6e;margin:0 auto}
.card h3{font-size:21px;font-weight:700;margin-top:22px}
.card p{font-size:12.5px;line-height:22px;margin-top:14px}
.card .go{position:absolute;right:10px;bottom:12px;width:30px;height:30px;border-radius:50%;background:var(--green)}
.card.featured{background:linear-gradient(160deg,#163c94,#0d1f5e);color:var(--white);border:none}
.card.featured .icon{background:var(--green);border:3px solid var(--white)}
.services .slider{left:548px;top:609px}
.services .slider span{background:var(--navy)}

/* why */
.why{top:1956px;height:800px}
.why .eyebrow{position:absolute;left:67px;top:52px}
.why h2{position:absolute;left:67px;top:95px;font-size:50px;line-height:62px}
.reason{position:absolute;left:65px;width:458px}
.reason .num{position:absolute;left:0;top:0;width:56px;height:56px;border-radius:50%;border:1.5px solid #bbb;background:var(--white);font-family:'Quicksand',sans-serif;font-weight:700;font-size:22px;color:var(--navy);display:flex;align-items:center;justify-content:center}
.reason h3{position:absolute;left:69px;top:6px;font-size:21px;font-weight:700}
.reason p{position:absolute;left:69px;top:50px;width:380px;font-size:14.5px;line-height:22px}
.reason.ruled::after{content:"";position:absolute;left:69px;right:0;top:141px;border-bottom:2px solid var(--line)}
.why-photo{position:absolute;left:572px;top:34px;width:564px;height:713px;border-radius:52px;background:linear-gradient(170deg,#e6e8eb,#c4ccd6 50%,#8fa0bd)}

/* cta */
.cta{top:2780px;height:391px;background:linear-gradient(180deg,#26309a,#2848d6)}
.cta-photo{position:absolute;left:16px;top:2755px;width:546px;height:416px;border-radius:180px 180px 0 0;background:linear-gradient(180deg,#e9ecf2,#aab9d8 70%,#7c93cc)}
.cta-body{position:absolute;left:676px;top:60px;width:440px;color:var(--white)}
.cta-body h2{font-family:'Quicksand',sans-serif;font-weight:700;font-size:49px;line-height:62px}
.cta-body p{font-size:14px;line-height:22px;margin-top:24px}
.cta-body .btn{background:var(--white);color:var(--navy);margin-top:22px;line-height:38px;font-size:13px}

/* hours + form */
.contact{top:3171px;height:619px}
.hours{position:absolute;left:62px;top:70px;width:476px;height:482px;border-radius:26px;background:linear-gradient(140deg,#182d8a,#0b1a5a 60%,#1d3a9c);color:var(--white);padding:36px 36px 0}
.hours h2{font-family:'Quicksand',sans-serif;font-weight:600;font-size:39px;line-height:62px}
.hours ul{margin-top:32px;list-style:none}
.hours li{display:flex;justify-content:space-between;font-size:14.5px;font-weight:600;padding:13px 0 18px;border-bottom:1.5px solid rgba(255,255,255,.55)}
.hours li:last-child{border-bottom:none}
.form{position:absolute;left:603px;top:70px;width:522px}
.form h2{font-size:40px;line-height:50px;margin-bottom:23px}
.field{height:49px;background:#f3f3f3;border:1px solid #e2e2e2;margin-bottom:13px;font-size:11px;padding:17px 26px}
.field.area{height:111px;padding-top:14px}
.form .btn{margin-top:1px;padding:0 26px;font-size:15px}

/* footer */
footer{top:3790px;height:411px;background:var(--footer);color:var(--white)}
.news{position:absolute;left:60px;top:40px;font-family:'Quicksand',sans-serif;font-weight:600;font-size:40px}
.email{position:absolute;left:650px;top:35px;width:327px;height:40px;border-radius:20px;background:var(--white);color:var(--ink);font-size:14px;font-weight:600;padding:11px 22px}
footer .sub{position:absolute;left:1009px;top:35px;line-height:40px;padding:0 25px;font-size:14px}
.flogo{position:absolute;left:70px;top:130px;font-weight:700;font-size:58px;letter-spacing:3px}
.fabout{position:absolute;left:66px;top:256px;width:230px;font-size:13.5px;line-height:16px}
.col{position:absolute;top:142px;font-size:14px;line-height:24px}
.col h4{font-size:14px;font-weight:700;margin-bottom:6px}
.col ul{list-style:none}
.bottom{position:absolute;left:60px;right:60px;top:363px;border-top:1px solid #777}
.copy{position:absolute;left:75px;top:380px;font-size:13.5px;display:flex;gap:30px}
.fsocial{position:absolute;left:1016px;top:381px;display:flex;gap:10px}
.fsocial .dot{width:14px;height:14px}
</style>
</head>
<body>

<div class="topbar">
  <div class="item" style="left:62px"><svg width="18" height="18" viewBox="0 0 18 18"><circle cx="9" cy="9" r="9" fill="#fff"/><rect x="4.5" y="5.5" width="9" height="7" fill="none" stroke="#141c63" stroke-width="1.2"/><path d="M4.5 5.5 9 9.5 13.5 5.5" fill="none" stroke="#141c63" stroke-width="1.2"/></svg>hello@velqoclinic.com</div>
  <div class="item" style="left:258px"><svg width="18" height="18" viewBox="0 0 18 18"><path d="M9 1C5.7 1 3.5 3.4 3.5 6.4 3.5 10.5 9 17 9 17s5.5-6.5 5.5-10.6C14.5 3.4 12.3 1 9 1z" fill="#fff"/><circle cx="9" cy="6.5" r="2" fill="#141c63"/></svg>Lorem junid kmsci.</div>
  <div class="item" style="left:452px"><svg width="18" height="18" viewBox="0 0 18 18"><circle cx="9" cy="9" r="9" fill="#fff"/><path d="M6 4.5l2 2-1 1.4c.6 1.3 1.6 2.3 2.9 2.9l1.4-1 2 2-1.2 1.5C8.6 13 5 9.4 4.6 5.7z" fill="#141c63"/></svg>+10205550187</div>
  <div class="social"><span class="dot"></span><span class="dot"></span><span class="dot"></span></div>
</div>

<header>
  <div class="logo">Velqo</div>
  <nav class="nav"><span class="active">Home</span><span>About</span><span>Services</span><span>Blog</span><span>Contact us</span></nav>
  <span class="btn">Book an Appointment</span>
</header>

<section class="hero">
  <div class="hero-photo" role="img" aria-label="Photo of a clinician preparing a patient's arm for an IV drip"></div>
  <div class="hero-text">
    <div class="welcome">Welcome to Velqo Hydration.</div>
    <h1>Your Health is<br>Our Priority</h1>
    <p>we provide high-quality, compassionate care for you and your family. Our team of dedicated professionals is committed to ensuring that every patient receives the best treatment and attention possible.</p>
    <span class="btn">Discover More</span>
  </div>
  <div class="slider" style="left:548px;top:505px"><span></span><span></span><span></span><span></span></div>
</section>

<section class="about">
  <div class="about-photo" role="img" aria-label="Photo of a modern treatment room with a doctor in the corner"></div>
  <div class="about-body">
    <div class="eyebrow">About Us</div>
    <h2 class="head">Affordable Health<br>Care Solutionsy</h2>
    <p>A brief statement outlining the purpose and mission of the clinic. This can include the commitment to patient care, community health, and any specifical goals for our values.</p>
    <ul class="features">
      <li><svg width="22" height="18" viewBox="0 0 22 18"><path d="M11 17 2 8.5C-.5 6 .8 1 5 1c2.6 0 4.6 1.5 6 3.4C12.4 2.5 14.4 1 17 1c4.2 0 5.5 5 3 7.5z" fill="#1c2786"/><path d="M5 9h4l1-2 2 4 1-2h4" fill="none" stroke="#fff" stroke-width="1.3"/></svg>Medical Professionals</li>
      <li><svg width="22" height="18" viewBox="0 0 22 18"><path d="M11 17 2 8.5C-.5 6 .8 1 5 1c2.6 0 4.6 1.5 6 3.4C12.4 2.5 14.4 1 17 1c4.2 0 5.5 5 3 7.5z" fill="#1c2786"/><path d="M5 9h4l1-2 2 4 1-2h4" fill="none" stroke="#fff" stroke-width="1.3"/></svg>Facilities and Equipment</li>
      <li><svg width="22" height="18" viewBox="0 0 22 18"><path d="M11 17 2 8.5C-.5 6 .8 1 5 1c2.6 0 4.6 1.5 6 3.4C12.4 2.5 14.4 1 17 1c4.2 0 5.5 5 3 7.5z" fill="#1c2786"/><path d="M5 9h4l1-2 2 4 1-2h4" fill="none" stroke="#fff" stroke-width="1.3"/></svg>Emergency Care</li>
      <li><svg width="22" height="18" viewBox="0 0 22 18"><path d="M11 17 2 8.5C-.5 6 .8 1 5 1c2.6 0 4.6 1.5 6 3.4C12.4 2.5 14.4 1 17 1c4.2 0 5.5 5 3 7.5z" fill="#1c2786"/><path d="M5 9h4l1-2 2 4 1-2h4" fill="none" stroke="#fff" stroke-width="1.3"/></svg>Medical Consulting</li>
      <li><svg width="22" height="18" viewBox="0 0 22 18"><path d="M11 17 2 8.5C-.5 6 .8 1 5 1c2.6 0 4.6 1.5 6 3.4C12.4 2.5 14.4 1 17 1c4.2 0 5.5 5 3 7.5z" fill="#1c2786"/><path d="M5 9h4l1-2 2 4 1-2h4" fill="none" stroke="#fff" stroke-width="1.3"/></svg>Services Offered</li>
      <li><svg width="22" height="18" viewBox="0 0 22 18"><path d="M11 17 2 8.5C-.5 6 .8 1 5 1c2.6 0 4.6 1.5 6 3.4C12.4 2.5 14.4 1 17 1c4.2 0 5.5 5 3 7.5z" fill="#1c2786"/><path d="M5 9h4l1-2 2 4 1-2h4" fill="none" stroke="#fff" stroke-width="1.3"/></svg>Specializations</li>
    </ul>
    <span class="btn">More About Us</span>
  </div>
</section>

<section class="services">
  <div class="eyebrow">Our Services</div>
  <h2 class="head">Our Velqo Hydration specialties<br>Technical service</h2>

  <div class="card" style="left:64px;width:249px">
    <div class="icon" role="img" aria-label="Icon of a care team"></div>
    <h3>Primary Care</h3>
    <p>Routine checkups, preventive care,<br>and health management.</p>
    <span class="go"></span>
  </div>
  <div class="card" style="left:333px;width:265px">
    <div class="icon" role="img" aria-label="Icon of a specialist at a desk"></div>
    <h3>Specialty Service</h3>
    <p>Cardiology, dermatology,<br>pediatrics, gynecology, etc.</p>
    <span class="go"></span>
  </div>
  <div class="card featured" style="left:618px;width:249px" role="img" aria-label="Laboratory service card on a blue digital network background">
    <div class="icon"></div>
    <h3 style="margin-top:16px">Laboratory</h3>
    <p>Blood tests, imaging, screenings,<br>etc.</p>
    <span class="go"></span>
  </div>
  <div class="card" style="left:885px;width:251px">
    <div class="icon" role="img" aria-label="Icon of a wellness program"></div>
    <h3>Wellness Programs</h3>
    <p>Weight management, fitness<br>plans, nutritional counseling, etc.</p>
    <span class="go"></span>
  </div>
  <div class="slider"><span></span><span></span><span></span><span></span></div>
</section>

<section class="why">
  <div class="eyebrow">Why Choose Us</div>
  <h2 class="head">We Are Always<br>Open For Your<br>Health Services</h2>

  <div class="reason ruled" style="top:307px">
    <div class="num">01</div>
    <h3>Compassionate &amp; Expert Care</h3>
    <p>Our team of dedicated healthcare professionals combines years of experience with a genuine commitment to providingvv</p>
  </div>
  <div class="reason ruled" style="top:460px">
    <div class="num">02</div>
    <h3>Patient-Centered Approach</h3>
    <p>Our team of dedicated healthcare professionals combines years of experience with a genuine commitment to providingvv</p>
  </div>
  <div class="reason" style="top:613px">
    <div class="num">03</div>
    <h3>Personalized Treatment Plans</h3>
    <p>Our team of dedicated healthcare professionals combines years of experience with a genuine commitment to providingvv</p>
  </div>

  <div class="why-photo" role="img" aria-label="Photo of a doctor holding the hand of a patient resting beside an IV stand"></div>
</section>

<section class="cta">
  <div class="cta-body">
    <h2>Get the Care You<br>Need – Book Now</h2>
    <p>A brief statement outlining the purpose and mission of the clinic. This can include the commitment to patient care, community health, and any specific goals or values.</p>
    <span class="btn">Book an Appointment</span>
  </div>
</section>
<div class="cta-photo" role="img" aria-label="Photo of a nurse in protective gear preparing a syringe"></div>

<section class="contact">
  <div class="hours">
    <h2>Visit Us During Our<br>Working Hours</h2>
    <ul>
      <li><span>Monday - Tuesday:</span><span>9am - 6pm</span></li>
      <li><span>Wednesday - Thursday:</span><span>9am - 6pm</span></li>
      <li><span>Friday:</span><span>9am - 6pm</span></li>
      <li><span>Saturday:</span><span>9am - 6pm</span></li>
      <li><span>Sunday:</span><span>9am - 6pm</span></li>
    </ul>
  </div>
  <div class="form">
    <h2 class="head">Make An Appointment</h2>
    <div class="field">Name :</div>
    <div class="field">Last Name :</div>
    <div class="field">Email :</div>
    <div class="field">Phone Number :</div>
    <div class="field area">How can I Help You ?</div>
    <span class="btn">Submit</span>
  </div>
</section>

<footer>
  <div class="news">Subscribe for newsletter</div>
  <div class="email">Email Address</div>
  <span class="btn sub">Subscribe</span>

  <div class="flogo">Velqo</div>
  <p class="fabout">Subscribe to out newsletter today to receive latest news administrate cost effective for tactical data.</p>

  <div class="col" style="left:395px"><h4>QUICK LINKS</h4><ul><li>Home</li><li>About Us</li><li>Services</li><li>Blogs</li><li>Contact Us</li></ul></div>
  <div class="col" style="left:650px;top:132px"><h4>CONTACT US</h4><ul><li>1800-555-0142</li><li>care@velqoclinic.com</li><li>Help &amp; Contact</li><li>FAQS</li></ul></div>
  <div class="col" style="left:989px"><h4>SERVICES</h4><ul><li>Primary Care</li><li>Specialty Service</li><li>Laboratory</li><li>Wellness Programs</li><li>Facilities</li><li>Equipment</li></ul></div>

  <div class="bottom"></div>
  <div class="copy"><span>© 2024 Velqo Hydration. All Rights Reserved.</span><span>Terms &amp; Conditions</span><span>Privacy Policy</span></div>
  <div class="fsocial"><span class="dot"></span><span class="dot"></span><span class="dot"></span><span class="dot"></span></div>
</footer>

</body>
</html>
```